Business Card Design Project

We have recently completed CraftHive projects for a new logo and wesbite.
We now require new business cards.
We hand out very little printed material to clients as all information is online. When we do hand out something, like a business card, we want it to have real impact and make a statement about the quality and professionalism of our company.
We have an idea of what we want our card to look like but we want a designer to make sure they have impact and look great.
Our requirements are…
Size: 85mm X 55mm - Landscape
Front of card: Logo plus the following contact information.
Dennis Marlow
Operations Manager
Phone +44(0) 1632 xxx xxx
Mobile +44(0) 7700 xxx xxx
Email denmo@korvantix.example
Address 17 Pellick Row, Aberdeen AB12 9QZ
Website www.korvantix.example
How you layout the front of the card is up to you, we would like to see some different ideas. Attached are two versions of our logo that may be used.
Back of card: We would like this to be simple but again have impact. Our current thought is to have the logo or just the large W design from the logo in white against a dark background, perhaps made up from the dark green in the logo.
The logos are attached so you can see the colours in them but the dark ones are..
Dark Blue = C:88, M:55, Y:44, K:28
Dark Green = C:87, M:53, Y:50, K:50
We sometimes also use a bright orange as an accent or highlight colour…
Orange: = C:0, M:39, Y:94, K:0

```html
<!DOCTYPE html>
<html lang="en">
<head>
<meta charset="utf-8">
<title>Korvantix business cards</title>
<link href="https://fonts.googleapis.com/css2?family=Open+Sans:wght@400;600;700;800&display=swap" rel="stylesheet">
<style>
  :root {
    --backdrop: #e8e5e1;
    --card: #ffffff;
    --ink-dark: #1f4250;
    --ink-mid: #2e4a56;
    --ink-label: #1e1e1e;
    --panel-top: #3c5f6f;
    --panel-bottom: #6fa6ae;
    --accent-orange: #f6a623;
    --deep-green: #123f48;
    --faint-teal: #4f8690;
  }
  * { box-sizing: border-box; margin: 0; padding: 0; }
  html, body { width: 1200px; height: 788px; overflow: hidden; }
  body {
    position: relative;
    background: var(--backdrop);
    font-family: "Open Sans", Arial, sans-serif;
  }
  .view-label {
    position: absolute;
    width: 300px;
    text-align: center;
    font-size: 22px;
    color: var(--ink-label);
  }
  .card {
    position: absolute;
    width: 502px;
    height: 325px;
    border-radius: 22px;
    background: var(--card);
    overflow: hidden;
    box-shadow: 0 4px 14px rgba(0,0,0,0.18);
  }
  .card--front { left: 85px; top: 57px; }
  .card--back-one { left: 626px; top: 54px; }
  .card--back-two { left: 65px; top: 444px; background: var(--deep-green); }
  .card--back-three { left: 626px; top: 444px; }

  .front-art { position: absolute; inset: 0; }

  .brand-name {
    position: absolute;
    font-weight: 800;
    color: var(--ink-dark);
    letter-spacing: 1px;
    text-align: center;
    white-space: nowrap;
  }
  .card--front .brand-name { left: 20px; width: 230px; top: 158px; font-size: 30px; }
  .card--back-one .brand-name { left: 0; width: 502px; top: 100px; font-size: 48px; letter-spacing: 3px; }
  .card--back-three .brand-name { left: 0; width: 502px; top: 168px; font-size: 56px; letter-spacing: 3px; }
  .card--back-two .brand-name {
    left: 0; width: 502px; top: 118px; font-size: 64px;
    color: var(--faint-teal); letter-spacing: 4px;
  }

  .address {
    position: absolute;
    left: 20px; width: 230px; top: 264px;
    text-align: center;
    font-size: 13px;
    line-height: 17px;
    color: #2a2a2a;
  }
  .person {
    position: absolute;
    left: 290px; width: 220px; top: 106px;
    text-align: center;
    color: #ffffff;
  }
  .person__name { font-size: 17px; font-weight: 700; line-height: 22px; }
  .person__role { font-size: 13px; line-height: 18px; color: #e2edf0; }
  .contacts {
    position: absolute;
    right: 9px; top: 218px;
    list-style: none;
    text-align: right;
    font-size: 12.5px;
    line-height: 21.5px;
    color: #ffffff;
  }
  .contacts b { font-weight: 700; margin-right: 3px; }
  .website {
    position: absolute;
    left: 0; width: 502px;
    text-align: center;
    font-size: 18px;
    letter-spacing: 3px;
    color: var(--ink-mid);
  }
  .card--back-one .website { top: 283px; }
  .card--back-three .website { top: 279px; }
</style>
</head>
<body>
  <div class="view-label" style="left:170px; top:18px;">Front</div>
  <div class="view-label" style="left:726px; top:18px;">Back - 1</div>
  <div class="view-label" style="left:174px; top:401px;">Back - 2</div>
  <div class="view-label" style="left:726px; top:401px;">Back - 3</div>

  <section class="card card--front">
    <svg class="front-art" viewBox="0 0 502 325" width="502" height="325" aria-hidden="true">
      <defs>
        <linearGradient id="panelFade" x1="0" y1="0" x2="0" y2="1">
          <stop offset="0" stop-color="var(--panel-top)"/>
          <stop offset="1" stop-color="var(--panel-bottom)"/>
        </linearGradient>
      </defs>
      <path d="M272 0 C318 60 308 150 288 210 C272 258 262 300 260 325 L502 325 L502 0 Z" fill="url(#panelFade)"/>
      <path d="M264 -2 C306 58 298 150 276 214 C265 248 258 272 255 298" fill="none" stroke="var(--accent-orange)" stroke-width="6" stroke-linecap="round"/>
    </svg>
    <div class="brand-name">KORVANTIX</div>
    <p class="address">17 Pellick Row<br>Aberdeen AB12 9QZ</p>
    <div class="person">
      <p class="person__name">Dennis Marlow</p>
      <p class="person__role">Operations Manager</p>
    </div>
    <ul class="contacts">
      <li><b>c</b>: +44(0) 7700 xxx xxx</li>
      <li><b>p</b>: +44(0) 1632 xxx xxx</li>
      <li><b>e</b>: denmo@korvantix.example</li>
      <li><b>w</b>: www.korvantix.example</li>
    </ul>
  </section>

  <section class="card card--back-one">
    <div class="brand-name">KORVANTIX</div>
    <p class="website">www.korvantix.example</p>
  </section>

  <section class="card card--back-two">
    <div class="brand-name">KORVANTIX</div>
  </section>

  <section class="card card--back-three">
    <div class="brand-name">KORVANTIX</div>
    <p class="website">www.korvantix.example</p>
  </section>
</body>
</html>
```